Business Card Design

New business card design

Target Market(s)

Residential & Commercial Property Managers

Industry/Entity Type

Plumbing Services

Contact Information for Business Card

Name - Rowan Keddle, title - Director, Phone Number - 0431 286 517, email - rowan@tbk-plumbing.com.au, Company ABN - 73 215 904 386,

Font styles to use
Sans Serif

Colors
0054AA
0677BA
7BADD7
CADEEF
E8F1F8

```html
<!DOCTYPE html>
<html lang="en">
<head>
<meta charset="utf-8">
<title>TBK Plumbing Services – Business Card</title>
<link href="https://fonts.googleapis.com/css2?family=Montserrat:wght@400;500;700&display=swap" rel="stylesheet">
<style>
  :root {
    --backdrop: #d3d8d8;
    --paper: #eeeeec;
    --navy: #121826;
    --ink: #1c2430;
    --sky: #2aa7e6;
    --ocean: #0677ba;
    --white: #f4f6f8;
  }
  * { box-sizing: border-box; margin: 0; padding: 0; }
  html, body {
    width: 1200px; height: 881px; overflow: hidden;
    background: var(--backdrop);
    font-family: "Montserrat", sans-serif;
  }
  .sheet {
    width: 1200px; height: 881px;
    display: flex; align-items: center; justify-content: center; gap: 48px;
  }
  .card {
    position: relative;
    width: 520px; height: 297px;
    box-shadow: 0 18px 40px rgba(40, 50, 60, 0.25);
  }
  /* front */
  .card--front {
    background: var(--paper);
    border-bottom: 3px solid var(--sky);
  }
  .brand {
    position: absolute; top: 34px; left: 170px;
    display: flex; align-items: center; gap: 10px;
  }
  .brand__dot {
    width: 14px; height: 14px; border-radius: 50%;
    background: var(--sky);
  }
  .brand__name {
    font-weight: 500; font-size: 22px; letter-spacing: 0.5px;
    color: var(--ink);
  }
  .abn {
    position: absolute; top: 100px; left: 90px;
    font-size: 14px; color: var(--ink);
  }
  .contact {
    position: absolute; left: 36px; bottom: 44px;
    list-style: none; font-size: 14px; color: var(--ink);
  }
  .contact li { display: flex; align-items: center; gap: 8px; line-height: 22px; }
  .contact svg { width: 12px; height: 12px; fill: var(--sky); }
  .person {
    position: absolute; right: 24px; bottom: 58px;
    text-align: right;
  }
  .person__name {
    font-weight: 700; font-size: 19px; color: var(--sky);
  }
  .person__title {
    font-size: 14px; color: var(--ink); margin-top: 2px;
  }
  .accent-bar {
    position: absolute; right: 0; bottom: 58px;
    width: 12px; height: 46px; background: var(--sky);
  }
  /* back */
  .card--back {
    background: var(--navy);
    border-bottom: 5px solid var(--ocean);
    display: flex; align-items: center; justify-content: center; gap: 16px;
  }
  .card--back .brand__dot { width: 22px; height: 22px; }
  .card--back .brand__name {
    color: var(--white); font-size: 34px; letter-spacing: 1px;
  }
</style>
</head>
<body>
<main class="sheet">
  <section class="card card--front" aria-label="Card front">
    <div class="brand">
      <span class="brand__dot"></span>
      <span class="brand__name">TBK Plumbing Services</span>
    </div>
    <p class="abn">Company ABN - 73 215 904 386</p>
    <ul class="contact">
      <li>
        <svg viewBox="0 0 24 24" aria-hidden="true"><path d="M6.6 10.8a15.1 15.1 0 0 0 6.6 6.6l2.2-2.2a1 1 0 0 1 1-.25 11.4 11.4 0 0 0 3.6.57 1 1 0 0 1 1 1V20a1 1 0 0 1-1 1A17 17 0 0 1 3 4a1 1 0 0 1 1-1h3.5a1 1 0 0 1 1 1c0 1.25.2 2.45.57 3.6a1 1 0 0 1-.25 1z"/></svg>
        0431 286 517
      </li>
      <li>
        <svg viewBox="0 0 24 24" aria-hidden="true"><path d="M2 5h20v14H2zm2 2v.5l8 5 8-5V7l-8 5z"/></svg>
        rowan@tbk-plumbing.com.au
      </li>
    </ul>
    <div class="person">
      <p class="person__name">Rowan Keddle</p>
      <p class="person__title">Director</p>
    </div>
    <span class="accent-bar"></span>
  </section>

  <section class="card card--back" aria-label="Card back">
    <span class="brand__dot"></span>
    <span class="brand__name">TBK Plumbing Services</span>
  </section>
</main>
</body>
</html>
```